Business card design needed

A laid back coffee shop that has a great feel, that becomes a bar and grill at night. We are also wanting to cater for functions etc.
The business itself is painted dark blue/charcoal and has red doors.
Would like a logo that will be recognised when seen.

Industry/Entity Type

Coffee Shop

Contact Information for Business Card

The Lantern Coffee Bar & Grill
14b Wattle St
Merrindale NSW 2291
Ph. 02 4817 6230

Logo Text

Logo styles of interest
Emblem Logo
Abstract Logo
Wordmark Logo
Requirements
Must have
• A loyalty card on the back with 2 rows of 7 stamp spaces and a place to write a name and phone number (for a draw)

```html
<!DOCTYPE html>
<html lang="en">
<head>
<meta charset="utf-8">
<title>The Lantern Coffee Bar &amp; Grill – Business Card</title>
<link href="https://fonts.googleapis.com/css2?family=Cutive+Mono&display=swap" rel="stylesheet">
<style>
  :root {
    --page: #ffffff;
    --card: #ffffff;
    --ink: #1e1e1e;
    --brand-red: #e8272a;
    --stamp-ring: #222222;
    --wash-deep: rgba(232, 168, 70, 0.55);
    --wash-light: rgba(245, 205, 120, 0.28);
    --card-shadow: 6px 8px 14px rgba(0, 0, 0, 0.45);
  }
  * { box-sizing: border-box; margin: 0; padding: 0; }
  html, body {
    width: 1200px; height: 1000px; overflow: hidden;
    background: var(--page);
    font-family: "Cutive Mono", "Courier New", monospace;
    color: var(--ink);
  }
  .canvas { position: relative; width: 1200px; height: 1000px; }

  .card {
    position: absolute; width: 623px; height: 355px;
    background: var(--card); box-shadow: var(--card-shadow);
    overflow: hidden;
  }
  .card--front { left: 288px; top: 109px; }
  .card--back { left: 292px; top: 533px; }

  .texture-wash {
    position: absolute; top: 0; height: 355px;
    background: linear-gradient(90deg,
      transparent 0%,
      var(--wash-light) 25%,
      var(--wash-deep) 55%,
      var(--wash-light) 80%,
      transparent 100%);
  }
  .card--front .texture-wash { left: 300px; width: 230px; }
  .card--back .texture-wash { left: 330px; width: 210px; }

  .front-mark {
    position: absolute; left: 104px; top: 42px;
    width: 118px; height: 118px; border-radius: 50%;
    border: 7px solid var(--brand-red);
  }
  .brand-name {
    position: absolute; left: 0; width: 330px; text-align: center;
    font-weight: 400; color: var(--ink);
  }
  .brand-name--title { top: 230px; font-size: 35px; letter-spacing: 0.5px; }
  .brand-name--sub { top: 280px; font-size: 17px; }

  .divider {
    position: absolute; left: 309px; top: 83px;
    width: 2px; height: 189px; background: var(--ink);
  }
  .address {
    position: absolute; left: 325px; top: 104px; width: 285px;
    text-align: center; font-size: 26px; line-height: 32.5px;
    letter-spacing: 0.6px; font-style: normal;
  }

  .stamp-grid {
    position: absolute; left: 95px; top: 33px;
    display: grid; grid-template-columns: repeat(7, 52px);
    column-gap: 13.6px; row-gap: 11px;
  }
  .stamp {
    width: 52px; height: 52px; border-radius: 50%;
    border: 2px solid var(--stamp-ring);
  }
  .field {
    position: absolute; display: flex; align-items: flex-end;
    font-size: 21px; letter-spacing: 0.5px;
  }
  .field__line {
    border-bottom: 1px dashed var(--ink); height: 1px; margin-bottom: 4px;
  }
  .field--name { left: 35px; top: 181px; }
  .field--name .field__label { width: 95px; }
  .field--name .field__line { width: 358px; }
  .field--phone { left: 34px; top: 245px; }
  .field--phone .field__label { width: 190px; }
  .field--phone .field__line { width: 264px; }
  .back-name {
    position: absolute; left: 36px; top: 292px;
    font-size: 22px; letter-spacing: 0.3px;
  }
  .back-mark {
    position: absolute; left: 500px; top: 210px;
    width: 82px; height: 82px; border-radius: 50%;
    border: 6px solid var(--brand-red);
  }
</style>
</head>
<body>
<main class="canvas">
  <section class="card card--front" aria-label="Business card front">
    <div class="texture-wash" role="img" aria-label="Coffee ring stain texture"></div>
    <div class="front-mark" aria-hidden="true"></div>
    <p class="brand-name brand-name--title">THE LANTERN</p>
    <p class="brand-name brand-name--sub">Coffee Bar &amp; Grill</p>
    <div class="divider"></div>
    <address class="address">
      14b Wattle St<br>
      Merrindale<br>
      NSW 2291<br>
      Ph. 02 4817 6230
    </address>
  </section>

  <section class="card card--back" aria-label="Loyalty card back">
    <div class="texture-wash" role="img" aria-label="Coffee ring stain texture"></div>
    <div class="stamp-grid" aria-label="Fourteen loyalty stamp spaces">
      <span class="stamp"></span><span class="stamp"></span><span class="stamp"></span><span class="stamp"></span><span class="stamp"></span><span class="stamp"></span><span class="stamp"></span>
      <span class="stamp"></span><span class="stamp"></span><span class="stamp"></span><span class="stamp"></span><span class="stamp"></span><span class="stamp"></span><span class="stamp"></span>
    </div>
    <div class="field field--name"><span class="field__label">Name</span><span class="field__line"></span></div>
    <div class="field field--phone"><span class="field__label">Phone Number</span><span class="field__line"></span></div>
    <p class="back-name">THE LANTERN Coffee Bar &amp; Grill</p>
    <div class="back-mark" aria-hidden="true"></div>
  </section>
</main>
</body>
</html>
```